Business Card for Multi-Brand Sportswear Company

We are looking for a business card which represents our company and the multiple brands within it.

The company: Fen Athletics (LTD)
The brands: Fen, TavaPuni, ElmStretch, Grit and Rain

Employees using these cards would be representing Fen Athletics, rather than any of the individual brands. You will see a current design within the uploaded files, to give some inspiration. The actual text of the brands is not necessary, but the logos should be on there is some format.

Our creative minds on this are stretched, so we are looking for someone to make this their own, and show us what a good business card should look like.

We may like to get these printed with spot gloss, so keep that in mind with your designs.

www.fenathletics.co.uk

Industry/Entity Type

Business

Contact Information for Business Card

Leo Pemberton-Hale
Operations Manager
(+44) 1632 960 418
Leo@fenathletics.co.uk
www.fenathletics.co.uk

Font styles to use
Sans Serif
Other font styles liked:
• Eurostile

Colors
ffffff

Requirements
Nice to have
• Dark (black) background

```html
<!DOCTYPE html>
<html lang="en">
<head>
<meta charset="utf-8">
<title>Fen Athletics – Business Card</title>
<link href="https://fonts.googleapis.com/css2?family=Exo+2:wght@400;600;700&display=swap" rel="stylesheet">
<style>
  :root {
    --backdrop: #2b2624;
    --card: #121212;
    --card-edge: #1c1c1c;
    --white: #ffffff;
    --soft: #d9d9d9;
    --grey: #8a8a8a;
    --red: #e3202b;
    --violet: #6b5a86;
  }
  * { box-sizing: border-box; margin: 0; padding: 0; }
  html, body { width: 1200px; height: 716px; overflow: hidden; }
  body {
    background: var(--backdrop);
    font-family: "Exo 2", sans-serif;
    position: relative;
  }
  .card {
    position: absolute;
    top: 208px;
    width: 520px;
    height: 300px;
    background: var(--card);
    border: 1px solid var(--card-edge);
    box-shadow: 0 12px 30px rgba(0,0,0,.45);
    overflow: hidden;
  }
  .card-front { left: 50px; }
  .card-back { left: 630px; background: #0f0f0f; }

  .brand-name {
    position: absolute;
    left: 34px;
    top: 80px;
    color: var(--white);
    font-size: 27px;
    font-weight: 700;
    letter-spacing: .5px;
    display: flex;
    align-items: center;
    gap: 8px;
  }
  .brand-name .dot {
    width: 10px; height: 10px; background: var(--red);
  }
  .divider {
    position: absolute;
    left: 252px;
    top: 42px;
    width: 1px;
    height: 120px;
    background: var(--grey);
  }
  .divider::before, .divider::after {
    content: "";
    position: absolute;
    left: -2px;
    width: 5px; height: 5px;
    border-radius: 50%;
    background: var(--soft);
  }
  .divider::before { top: -2px; }
  .divider::after { bottom: -2px; }

  .contact {
    position: absolute;
    left: 272px;
    top: 44px;
    color: var(--white);
  }
  .contact .person {
    color: var(--red);
    font-size: 20px;
    font-weight: 700;
  }
  .contact .role {
    font-size: 14px;
    color: var(--soft);
    margin-bottom: 10px;
  }
  .contact .line {
    display: flex;
    align-items: center;
    gap: 8px;
    font-size: 14px;
    line-height: 22px;
  }
  .contact .line svg { width: 11px; height: 11px; flex: none; }

  .brand-row {
    position: absolute;
    left: 40px;
    top: 196px;
    display: flex;
    align-items: center;
    gap: 18px;
  }
  .badge-violet { width: 34px; height: 22px; background: var(--violet); }
  .badge-red { width: 26px; height: 26px; border: 2px solid var(--red); }
  .badge-white { width: 44px; height: 12px; background: var(--white); }
  .badge-circle { width: 20px; height: 20px; border: 2px solid var(--grey); border-radius: 50%; }

  .swoop { position: absolute; left: 0; bottom: 0; }

  .back-mark {
    position: absolute;
    left: 0; right: 0; top: 118px;
    display: flex;
    justify-content: center;
    align-items: center;
    gap: 14px;
    color: #6f6f6f;
    font-size: 44px;
    font-weight: 700;
    letter-spacing: 1px;
  }
  .back-mark .dot { width: 16px; height: 16px; background: var(--red); }
</style>
</head>
<body>
  <section class="card card-front">
    <div class="brand-name">Fen Athletics<span class="dot"></span></div>
    <div class="divider"></div>
    <div class="contact">
      <p class="person">Leo Pemberton-Hale</p>
      <p class="role">Operations Manager</p>
      <p class="line">
        <svg viewBox="0 0 12 12"><path d="M2 1h3l1 3-2 1a7 7 0 0 0 3 3l1-2 3 1v3c-6 1-10-3-9-9z" fill="var(--red)"/></svg>
        (+44) 1632 960 418
      </p>
      <p class="line">
        <svg viewBox="0 0 12 12"><rect x="1" y="2.5" width="10" height="7" fill="var(--red)"/><path d="M1 3l5 4 5-4" stroke="#121212" fill="none"/></svg>
        Leo@fenathletics.co.uk
      </p>
      <p class="line">
        <svg viewBox="0 0 12 12"><circle cx="6" cy="6" r="5" fill="var(--red)"/><path d="M1 6h10M6 1c-3 3-3 7 0 10M6 1c3 3 3 7 0 10" stroke="#121212" fill="none" stroke-width=".8"/></svg>
        www.fenathletics.co.uk
      </p>
    </div>
    <div class="brand-row" aria-label="Group brands">
      <span class="badge-violet" role="img" aria-label="TavaPuni"></span>
      <span class="badge-red" role="img" aria-label="Grit and Rain"></span>
      <span class="badge-white" role="img" aria-label="Fen"></span>
      <span class="badge-circle" role="img" aria-label="ElmStretch"></span>
    </div>
    <svg class="swoop" width="300" height="70" viewBox="0 0 300 70">
      <path d="M0 22 Q150 6 262 22 Q290 40 300 70 L0 70 Z" fill="var(--red)"/>
      <path d="M0 40 Q150 26 250 40 Q280 56 288 70 L0 70 Z" fill="var(--card)"/>
    </svg>
  </section>

  <section class="card card-back">
    <div class="back-mark">Fen Athletics<span class="dot"></span></div>
  </section>
</body>
</html>
```